Dunmore Roofing

Want a professional looking business card

Industry/Entity Type

Business

Contact Information for Business Card

Paul Dunmore ( Owner) paul@dunmoreroofing-example.com, www.dunmoreroofing-example.com, Adress: 4172 Township road 43 Alderbrook,ON K9X4T2

```html
<!DOCTYPE html>
<html lang="en">
<head>
<meta charset="utf-8">
<title>Dunmore Roofing – Business Card</title>
<link href="https://fonts.googleapis.com/css2?family=Roboto:wght@400;900&family=Roboto+Condensed:wght@700&display=swap" rel="stylesheet">
<style>
  :root {
    --stage: #2e2e2f;
    --card-grey: #77787b;
    --card-white: #f3f3f3;
    --brand-blue: #1a4384;
    --roof-grey: #7c7d80;
    --text-white: #ffffff;
    --text-soft: #e9edf5;
  }
  * { margin: 0; padding: 0; box-sizing: border-box; }
  html, body { width: 1200px; height: 960px; overflow: hidden; }
  body {
    background: var(--stage);
    font-family: "Roboto", Arial, sans-serif;
    position: relative;
  }
  .card {
    position: absolute;
    left: 320px;
    width: 600px;
    height: 342px;
    border-radius: 18px;
    overflow: hidden;
  }
  .wordmark { position: absolute; left: 0; right: 0; text-align: center; font-weight: 900; }
  .wordmark-top { display: block; font-size: 38px; line-height: 32px; letter-spacing: 2px; padding-left: 2px; }
  .wordmark-bottom { display: block; font-size: 14px; line-height: 14px; letter-spacing: 16px; padding-left: 16px; margin-top: 6px; }

  /* Back side */
  .card--back {
    top: 108px;
    background: var(--card-grey);
    color: var(--text-white);
  }
  .card--back .wordmark { top: 134px; color: var(--text-white); }
  .card--back .site {
    position: absolute;
    left: 0; right: 0; top: 192px;
    text-align: center;
    font-size: 14px;
    line-height: 16px;
    letter-spacing: 2.2px;
    color: var(--text-soft);
  }

  /* Front side */
  .card--front {
    top: 493px;
    background: var(--card-white);
  }
  .card--front .wordmark { top: 104px; color: var(--brand-blue); }
  .band {
    position: absolute;
    left: 0; top: 0;
    width: 600px; height: 342px;
  }
  .contact-list {
    position: absolute;
    left: 28px; top: 257px;
    list-style: none;
    font-size: 15px;
    line-height: 19.5px;
    color: var(--text-white);
  }
  .contact-list li { display: flex; align-items: center; gap: 8px; }
  .contact-list svg { width: 13px; height: 13px; flex: none; }
  .person {
    position: absolute;
    right: 25px; top: 222px;
    text-align: right;
    color: var(--text-white);
  }
  .person-name {
    font-family: "Roboto Condensed", Arial, sans-serif;
    font-weight: 700;
    font-size: 24px;
    line-height: 1;
  }
  .person-role {
    font-weight: 400;
    font-size: 15px;
    line-height: 18px;
    margin-top: 4px;
  }
  .person-address {
    font-style: normal;
    font-size: 15px;
    line-height: 19.5px;
    margin-top: 6px;
  }
</style>
</head>
<body>

<section class="card card--back" aria-label="Business card back">
  <div class="wordmark">
    <span class="wordmark-top">DUNMORE</span>
    <span class="wordmark-bottom">ROOFING</span>
  </div>
  <div class="site">www.dunmoreroofing-example.com</div>
</section>

<section class="card card--front" aria-label="Business card front">
  <div class="wordmark">
    <span class="wordmark-top">DUNMORE</span>
    <span class="wordmark-bottom">ROOFING</span>
  </div>

  <svg class="band" viewBox="0 0 600 342" aria-hidden="true">
    <polygon points="0,193 498,193 532,163 566,193 600,193 600,342 0,342" fill="var(--brand-blue)"/>
    <polyline points="0,191 494,191 532,158 570,191 600,191" fill="none" stroke="var(--roof-grey)" stroke-width="5"/>
    <rect x="529" y="180" width="7" height="7" fill="var(--text-white)"/>
  </svg>

  <ul class="contact-list">
    <li>
      <svg viewBox="0 0 24 24"><path fill="#fff" d="M6.6 10.8a15.1 15.1 0 0 0 6.6 6.6l2.2-2.2c.3-.3.7-.4 1-.2 1.1.4 2.3.6 3.6.6.6 0 1 .4 1 1V20c0 .6-.4 1-1 1A17 17 0 0 1 3 4c0-.6.4-1 1-1h3.5c.6 0 1 .4 1 1 0 1.3.2 2.5.6 3.6.1.3 0 .7-.2 1z"/></svg>
      <span>613 555 0148</span>
    </li>
    <li>
      <svg viewBox="0 0 24 24"><path fill="#fff" d="M2 5h20v14H2z"/><path fill="none" stroke="var(--brand-blue)" stroke-width="2" d="M2 6l10 7 10-7"/></svg>
      <span>paul@dunmoreroofing-example.com</span>
    </li>
    <li>
      <svg viewBox="0 0 24 24"><circle cx="12" cy="12" r="10" fill="#fff"/><path fill="none" stroke="var(--brand-blue)" stroke-width="1.6" d="M2 12h20M12 2c3 3 3 17 0 20M12 2c-3 3-3 17 0 20"/></svg>
      <span>www.dunmoreroofing-example.com</span>
    </li>
  </ul>

  <div class="person">
    <div class="person-name">PAUL DUNMORE</div>
    <div class="person-role">OWNER</div>
    <address class="person-address">4172 Township road 43<br>Alderbrook, ON K9X4T2</address>
  </div>
</section>

</body>
</html>
```